Northfield Builders Guild Business card

We are looking for a new business card design with photo included.
Our business is a nonprofit construction contractor membership organization. We offer business education, assist with business setup and licensing, provide safety training, and provide a member directory.
URL: www.builderslinkguild.org
Color code:
CMYK: 0 cyan, 42 magenta, 100 yellow, 0 black for Print.
Hexidecimal: #FF9900
RGB: R 255; G 153; B 0

```html
<!DOCTYPE html>
<html lang="en">
<head>
<meta charset="utf-8">
<title>Northfield Builders Guild – Business Card</title>
<link href="https://fonts.googleapis.com/css2?family=Open+Sans:wght@400;600;800&display=swap" rel="stylesheet">
<style>
  :root {
    --bg: #1c1c1c;
    --card: #1f1f1f;
    --card-edge: #2a2a2a;
    --orange: #ff9900;
    --white: #ffffff;
    --text: #e6e6e6;
    --muted-logo: #8c8c8c;
    --photo-dark: #262626;
    --photo-mid: #2e3e63;
  }
  * { margin: 0; padding: 0; box-sizing: border-box; }
  html, body { width: 1200px; height: 900px; overflow: hidden; }
  body {
    background: var(--bg);
    font-family: "Open Sans", Arial, sans-serif;
    display: flex;
    flex-direction: column;
    align-items: center;
    justify-content: center;
    gap: 36px;
  }
  .card {
    position: relative;
    width: 700px;
    height: 400px;
    background: var(--card);
    border: 1px solid var(--card-edge);
    box-shadow: 0 14px 30px rgba(0,0,0,0.55);
    overflow: hidden;
  }
  /* Front */
  .brand {
    position: absolute;
    left: 52px;
    top: 40px;
    font-weight: 800;
    color: var(--white);
    text-transform: uppercase;
    line-height: 1.02;
    letter-spacing: 0.5px;
  }
  .brand-name { font-size: 30px; }
  .brand-sub { font-size: 12px; letter-spacing: 9px; margin-top: 6px; }
  .person { position: absolute; left: 52px; top: 142px; }
  .person-name {
    color: var(--orange);
    font-weight: 600;
    font-size: 22px;
    text-transform: uppercase;
    letter-spacing: 0.5px;
  }
  .person-title { color: var(--text); font-size: 15px; margin-top: 2px; }
  .address {
    position: absolute; left: 52px; top: 210px;
    color: var(--text); font-size: 15px; line-height: 1.45;
  }
  .contacts {
    position: absolute; left: 52px; top: 272px;
    list-style: none; color: var(--text); font-size: 15px; line-height: 1.55;
  }
  .contacts li { display: flex; align-items: center; gap: 7px; }
  .contacts svg { width: 12px; height: 12px; flex: none; }
  .photo {
    position: absolute;
    right: 0; bottom: 0;
    width: 300px; height: 290px;
    background:
      radial-gradient(ellipse at 58% 30%, #b58d78 0 18%, transparent 34%),
      linear-gradient(180deg, var(--photo-dark) 0%, var(--photo-dark) 45%, var(--photo-mid) 70%, #24314f 100%);
  }
  /* Back */
  .card-back { display: flex; align-items: center; justify-content: center; }
  .back-brand {
    font-weight: 800;
    color: var(--muted-logo);
    text-transform: uppercase;
    text-align: center;
    line-height: 1.05;
  }
  .back-brand .brand-name { font-size: 44px; }
  .back-brand .brand-sub { font-size: 16px; letter-spacing: 14px; margin-top: 10px; }
</style>
</head>
<body>
  <section class="card card-front">
    <div class="brand">
      <div class="brand-name">Northfield<br>Builders</div>
      <div class="brand-sub">Guild</div>
    </div>
    <div class="person">
      <div class="person-name">Daniel Harlow</div>
      <div class="person-title">President</div>
    </div>
    <div class="address">
      2450 Cedar Ridge Rd., Suite #210<br>
      Millbrook, OR 97004
    </div>
    <ul class="contacts">
      <li>
        <svg viewBox="0 0 24 24" aria-hidden="true"><path fill="#ff9900" d="M6.6 10.8a15.1 15.1 0 0 0 6.6 6.6l2.2-2.2a1 1 0 0 1 1-.25 11.4 11.4 0 0 0 3.6.57 1 1 0 0 1 1 1V20a1 1 0 0 1-1 1A17 17 0 0 1 3 4a1 1 0 0 1 1-1h3.5a1 1 0 0 1 1 1c0 1.25.2 2.45.57 3.57a1 1 0 0 1-.25 1z"/></svg>
        (555) 318-2740
      </li>
      <li>
        <svg viewBox="0 0 24 24" aria-hidden="true"><rect x="2" y="5" width="20" height="14" fill="#ff9900"/><path d="M2 5l10 8 10-8" fill="none" stroke="#1f1f1f" stroke-width="2"/></svg>
        support@nfbguild.org
      </li>
      <li>
        <svg viewBox="0 0 24 24" aria-hidden="true"><circle cx="12" cy="12" r="10" fill="#ff9900"/><path d="M2 12h20M12 2c3 3 3 17 0 20M12 2c-3 3-3 17 0 20" fill="none" stroke="#1f1f1f" stroke-width="1.6"/></svg>
        www.builderslinkguild.org
      </li>
    </ul>
    <div class="photo" role="img" aria-label="Portrait photo of the president in a navy blazer and white shirt"></div>
  </section>

  <section class="card card-back">
    <div class="back-brand">
      <div class="brand-name">Northfield<br>Builders</div>
      <div class="brand-sub">Guild</div>
    </div>
  </section>
</body>
</html>
```